Revamp our wedding venue website

Currently we are using wordpress for our website and hoped to find a designer that can assist us with making the website prettier and more pleasing and draw more interest. www.velmorhall.com is our current site. We are connected to google business mail, so I would prefer to stay with this for now and update our gallery with new photos, blog page and putting the contact us form back on all the pages.

Target Market(s)

20-40 years of age, all ranges of styles and generally clients looking for a different modern feel vs. a hotel hall.

Industry/Entity Type

Wedding

Logo Text

1927 Velmor Hall

Number of Pages Required

4 page

Font styles to use
Serif

Requirements
Must have
• Light, airy feel. Romantic and informative. Mobile friendly and easy to contact us-preferred contact form on all pages. Gallery of photos. Previous reviews
Nice to have
• Bio of staff, maybe some videos, and fun things to do in the area for out of town guests. Maps and also venue blank floor plan.

```html
<!DOCTYPE html>
<html lang="en">
<head>
<meta charset="utf-8">
<title>Velmor Hall – Weddings &amp; Events</title>
<link rel="stylesheet" href="https://fonts.googleapis.com/css2?family=Roboto:wght@400;500;700&family=Roboto+Slab:wght@700&family=Open+Sans:wght@400;600;700&family=Courgette&display=swap">
<style>
:root{
  --red:#e62e48;
  --red-dark:#c9203a;
  --ink:#222;
  --grey-text:#777;
  --light-bg:#f5f5f5;
  --review-bg:#e3e3e3;
  --nav-dark:#1f1f1f;
  --footer:#222;
  --white:#fff;
  --star:#f2a93b;
}
*{margin:0;padding:0;box-sizing:border-box}
html,body{width:1200px;height:2601px;overflow:hidden;background:var(--white)}
body{position:relative;font-family:'Open Sans',sans-serif;color:var(--ink)}
.abs{position:absolute}

/* header */
.site-header{position:absolute;left:0;top:0;width:1200px;height:118px;background:var(--white);border-bottom:3px solid var(--red)}
.brand{left:99px;top:42px;font-family:'Roboto',sans-serif;font-weight:500;font-size:29px;color:var(--red);letter-spacing:.5px}
.tagline{right:99px;top:26px;display:flex;align-items:center;gap:10px;font-family:'Courgette',cursive;font-size:14px;color:var(--ink)}
.tagline .dot{width:30px;height:30px;border-radius:50%;background:var(--red);display:flex;align-items:center;justify-content:center}
.tagline em{font-style:normal;color:var(--red)}
.main-nav{left:385px;top:76px;display:flex;gap:3px}
.main-nav a{display:block;width:117px;height:42px;line-height:42px;text-align:center;background:var(--nav-dark);color:var(--white);font-family:'Roboto',sans-serif;font-size:12px;text-decoration:none}
.main-nav a.active{background:var(--red)}

/* hero */
.hero{left:0;top:118px;width:1200px;height:534px;background:linear-gradient(135deg,#6b5a3a 0%,#c8a878 35%,#e7d3c0 50%,#8a6a4e 70%,#3f3a2c 100%)}
.hero-arrow{top:242px;width:40px;height:40px;border:2px solid rgba(255,255,255,.7);border-radius:50%}
.hero-title{left:99px;top:355px;width:511px;height:94px;background:rgba(230,46,72,.9);font-family:'Roboto Slab',serif;font-size:50px;color:var(--white);padding:14px 0 0 22px}
.hero-text{left:99px;top:449px;width:511px;height:85px;background:rgba(0,0,0,.55);color:var(--white);font-size:14px;line-height:26px;padding:20px 0 0 24px}

/* welcome */
.welcome{left:0;top:652px;width:1200px;height:472px;background:var(--light-bg)}
.welcome-frame{left:118px;top:67px;width:295px;height:338px;background:var(--red);transform:skewY(-2deg)}
.welcome-photo{left:104px;top:58px;width:298px;height:351px;background:linear-gradient(160deg,#e8e4dc,#b9a89a 55%,#6e6259);border:6px solid var(--white);transform:skewY(-2deg)}
.welcome-body{left:527px;top:60px;width:575px}
.welcome-body h2{font-family:'Roboto',sans-serif;font-weight:500;font-size:30px}
.welcome-body .lead{color:var(--red);font-size:14px;margin-top:10px}
.welcome-body p{color:var(--grey-text);font-size:12px;line-height:24px;margin-top:16px}
.btn{display:inline-block;background:var(--red);color:var(--white);font-family:'Roboto',sans-serif;font-size:12px;text-decoration:none}
.welcome-body .btn{margin-top:26px;padding:12px 19px}

/* video band */
.video-band{left:0;top:1124px;width:1200px;height:399px;background:var(--red)}
.video-band svg{position:absolute;left:0;top:0}
.video-copy{left:99px;top:84px;width:270px;color:var(--white)}
.video-copy h3{font-family:'Roboto',sans-serif;font-weight:500;font-size:25px;line-height:40px}
.video-copy blockquote{font-style:italic;font-size:11px;line-height:22px;margin-top:14px}
.video-copy cite{display:block;font-style:normal;font-weight:700;font-size:11px}

/* events */
.events{left:0;top:1523px;width:1200px;height:558px;text-align:center}
.events h2{position:absolute;left:0;top:52px;width:1200px;font-family:'Roboto',sans-serif;font-weight:500;font-size:30px}
.events .intro{position:absolute;left:290px;top:100px;width:620px;font-size:12px;line-height:22px;color:var(--grey-text)}
.event-card{position:absolute;top:177px;width:307px}
.event-card .thumb{height:190px;border:4px solid #eee}
.event-card h4{font-size:13px;font-weight:700;margin-top:24px}
.event-card p{font-size:12px;line-height:22px;color:var(--grey-text);margin-top:6px}
.event-card .btn{margin-top:14px;padding:10px 12px;font-size:11px}

/* gallery & reviews */
.lower{left:0;top:2081px;width:1200px;height:394px}
.lower svg{position:absolute;left:0;top:0}
.gallery-title,.reviews-title{font-family:'Roboto',sans-serif;font-weight:500;font-size:22px}
.gallery-title{left:99px;top:42px;color:var(--white)}
.reviews-title{left:762px;top:42px;color:var(--ink)}
.pager{font-size:16px;letter-spacing:8px;font-weight:700}
.thumb-g{position:absolute;width:156px;height:112px;border:3px solid var(--white)}
.review{position:absolute;left:762px;width:345px;font-size:12px;line-height:22px;color:#555}
.review .more{font-size:10px;color:var(--red)}
.review .stars{color:var(--star);letter-spacing:2px;margin-left:6px}

/* footer */
.site-footer{left:0;top:2475px;width:1200px;height:126px;background:var(--footer);color:var(--white)}
.footer-links{left:99px;top:38px;font-size:12px}
.copyright{left:99px;top:72px;font-size:12px}
.connect{left:828px;top:40px;display:flex;align-items:center;gap:10px;font-size:12px}
.social{width:38px;height:38px;border-radius:50%;background:var(--white)}
</style>
</head>
<body>

<header class="site-header">
  <div class="abs brand">Velmor Hall</div>
  <div class="abs tagline">
    <span class="dot"><svg width="14" height="13" viewBox="0 0 14 13"><path d="M7 12.5 1.2 6.8A3.4 3.4 0 0 1 7 2.2a3.4 3.4 0 0 1 5.8 4.6Z" fill="#fff"/></svg></span>
    <span>Tampa's Most Unique Wedding and <em>Events Venue 813.555.0142</em></span>
  </div>
  <nav class="abs main-nav">
    <a class="active" href="#">HOME</a><a href="#">WEDDINGS</a><a href="#">EVENTS</a><a href="#">CATERING</a><a href="#">GALLERY</a><a href="#">CONTACT US</a>
  </nav>
</header>

<section class="abs hero" role="img" aria-label="Newlywed couple smiling as guests toss confetti outdoors">
  <span class="abs hero-arrow" style="left:32px"></span>
  <span class="abs hero-arrow" style="right:32px"></span>
</section>
<div class="abs hero-title">Weddings &amp; Events</div>
<div class="abs hero-text">Nemo enim ipsam voluptatem quia voluptas sit aspernatur aut odit<br>aut fugit, sed quia consequuntur magni dolores...</div>

<section class="abs welcome">
  <div class="abs welcome-frame"></div>
  <div class="abs welcome-photo" role="img" aria-label="Bride and wedding guests celebrating at a reception table"></div>
  <div class="abs welcome-body">
    <h2>Welcome to Velmor Hall</h2>
    <div class="lead">Imagine your wedding or event in Tampa's premiere, unique and historic venue</div>
    <p>When choosing the location for your wedding or event, the 1927 Velmor Hall provides you with an all-inclusive experience, from the moment you arrive, through the creative food, and amazing photo opportunities. The unique open-kitchen provides you, and your guests a front-row seat to our creative, serves up wonderful libations and specialty cocktails that enhance your experience...</p>
    <p>Watch this short video to find out more about having your event here at the 1927 Velmor Hall. Then, look around the site, check out the photos, and then call or contact our wedding and event specialists today, to check date availability, and to arrange your personal tour of the 1927 Velmor Hall...</p>
    <a class="btn" href="#">Learn More Info</a>
  </div>
</section>

<section class="abs video-band">
  <svg width="1200" height="399" viewBox="0 0 1200 399">
    <defs>
      <linearGradient id="hall" x1="0" y1="0" x2="1" y2="1">
        <stop offset="0" stop-color="#5a1a22"/><stop offset=".5" stop-color="#2a1216"/><stop offset="1" stop-color="#120a0c"/>
      </linearGradient>
    </defs>
    <polygon points="333,0 1102,0 1163,399 411,399" fill="url(#hall)" role="img" aria-label="Reception hall with red uplighting, set tables and a wedding cake"/>
    <circle cx="757" cy="200" r="37" fill="rgba(255,255,255,.55)"/>
    <polygon points="746,181 746,219 776,200" fill="#2a1216"/>
  </svg>
  <div class="abs video-copy">
    <h3>Weddings &amp; Events<br>at the 1927<br>Velmor Hall</h3>
    <blockquote>“It's been almost a month since my wedding at the Velmor Hall and I am still with my mouth open, it was absolutely beautiful.”</blockquote>
    <cite>– Marisa &amp; Daniel, Tampa, FL</cite>
  </div>
</section>

<section class="abs events">
  <h2>Events</h2>
  <p class="intro">We cater to a variety of events, such as, Weddings, Rehearsal Dinners, Fashion Shows, Anniversary parties, Bar/Bat Mitzvah's, Corporate Meetings/Seminars, and Fundraisers.</p>
  <div class="event-card" style="left:101px">
    <div class="thumb" role="img" aria-label="Hall set for a corporate meeting with long tables" style="background:linear-gradient(180deg,#cfd4e0,#3b4a7a 60%,#1c2140)"></div>
    <h4>Corporate Events</h4>
    <p>The Velmor Hall is the perfect venue for your next<br>professional event. Out of the ever...</p>
    <a class="btn" href="#">Learn More Info</a>
  </div>
  <div class="event-card" style="left:447px">
    <div class="thumb" role="img" aria-label="Dark hall with cocktail tables in white and green linens" style="background:linear-gradient(180deg,#3a3a40,#15151a 60%,#2c4a3a)"></div>
    <h4>Private Events</h4>
    <p>Private events include special Bar/Bat Mitzvah,<br>Quinceañera, Confirmation Party...</p>
    <a class="btn" href="#">Learn More Info</a>
  </div>
  <div class="event-card" style="left:792px">
    <div class="thumb" role="img" aria-label="Fashion show models posing on a purple-lit stage" style="background:linear-gradient(180deg,#8a5ab8,#c69fd6 50%,#5b3a78)"></div>
    <h4>Public Events</h4>
    <p>Think of the Velmor Hall when you need to<br>promote, host or organize...</p>
    <a class="btn" href="#">Learn More Info</a>
  </div>
</section>

<section class="abs lower">
  <svg width="1200" height="394" viewBox="0 0 1200 394">
    <rect width="1200" height="394" fill="var(--review-bg)"/>
    <polygon points="0,0 732,0 647,394 0,394" fill="var(--red)"/>
  </svg>
  <div class="abs gallery-title">Gallery</div>
  <div class="abs pager" style="left:585px;top:44px;color:#fff">‹›</div>
  <div class="thumb-g" style="left:99px;top:92px;background:linear-gradient(160deg,#4a5a80,#9aa4c0)" role="img" aria-label="Model on a runway"></div>
  <div class="thumb-g" style="left:276px;top:92px;background:linear-gradient(160deg,#2a2f70,#b05080)" role="img" aria-label="Hall lit in blue and pink"></div>
  <div class="thumb-g" style="left:453px;top:92px;background:linear-gradient(160deg,#6a5a8a,#2a2430)" role="img" aria-label="Speaker with a microphone"></div>
  <div class="thumb-g" style="left:99px;top:229px;background:linear-gradient(160deg,#d6d0c6,#7a6e60)" role="img" aria-label="Empty venue interior"></div>
  <div class="thumb-g" style="left:276px;top:229px;background:linear-gradient(160deg,#3a3430,#9a8a70)" role="img" aria-label="Dining tables set for dinner"></div>
  <div class="thumb-g" style="left:453px;top:229px;background:linear-gradient(160deg,#5a4a5a,#c0909a)" role="img" aria-label="Group of guests posing together"></div>

  <div class="abs reviews-title">Clients Reviews</div>
  <div class="abs pager" style="left:1075px;top:44px;color:#666">‹›</div>
  <div class="review" style="top:88px">My fiancé and I are extremely excited to start planning our wedding at this amazing venue! Carla and the...<br><span class="more">Read More &gt;&gt;</span><span class="stars">★★★★★</span></div>
  <div class="review" style="top:184px">Perfection My husband and I just got married this past week end and we were so fortunate that the 1927...<br><span class="more">Read More &gt;&gt;</span><span class="stars">★★★★★</span></div>
  <div class="review" style="top:282px">If you are tired of the beach theme wedding and we all know its too hot in Florida for a barn/garden wedding...<br><span class="more">Read More &gt;&gt;</span><span class="stars">★★★★★</span></div>
</section>

<footer class="abs site-footer">
  <div class="abs footer-links">Home &nbsp;/&nbsp; Weddings &nbsp;/&nbsp; Events &nbsp;/&nbsp; Catering &nbsp;/&nbsp; Gallery &nbsp;/&nbsp; Contact Us</div>
  <div class="abs copyright">Copyrights © 2016 . velmorhall | Allrights Reserved.</div>
  <div class="abs connect">
    <span>Connect With Us :</span>
    <span class="social"></span><span class="social"></span><span class="social"></span><span class="social"></span>
  </div>
</footer>

</body>
</html>
```